Business Card: RW Office Partners - Your organised problem solver

Business Name: RW Office Partners
Website: www.rwofficepartners.com.au
Email: marisol@rwofficepartners.com.au
Mobile: 61 482 907 236
Facebook: @rwofficepartners
Instrgram: @rwofficepartners

Brading Colours:
HEX
#986474
#ddccd3
#7a8498
#c9d8e4
#000000
#ffffff

Tag Line: Your organised problem solver

Link to DRAFT website:
https://deskhelpcollective.wixsite.com/rw-office-partners

About Page from the website:
My name is Marisol Wrenfield, and I would love to assist you to become more productive in your day to day and achieve your business and personal goals.
My mission is to give you time, time to work on the important tasks of your business or to be able to spend more time with your family. I will take on the tasks you don’t have time for, don’t know well or simply don’t like to do.
I have an extensive background in Administration, Tender Coordination, Document Control, WHS and Quality Management working primarily in the Construction, Mining and Corporate World.
I am passionate about being organised, having order and making things in your life (and mine) easier! I love to watch something unfold and grow into something amazing! I am known for being the go-to problem solver, the organiser of all things, producing high standards of work even under pressure. I’m also a confident communicator, and I understand that you’re busy running your business.

Target Market(s)

Small to Medium Business who require assistance in their business by a virtual assistant.

Industry/Entity Type

Virtual Assistant

Contact Information for Business Card

Mobile: 61 482 907 236

Font styles to use
Sans Serif

Colors
ffffff

Requirements
Must have
• Branding Colours as outlined.
Contact Details as outlined.
Logo as provided.
Proper contact details - mobile, facebook, instragm, website.
Simple, Elegant, very clean looking.
Should not have
• Note cute with pictures.
Not too girly as still want to market to construction companies.

```html
<!DOCTYPE html>
<html lang="en">
<head>
<meta charset="utf-8">
<title>RW Office Partners – Business Card</title>
<link href="https://fonts.googleapis.com/css2?family=Montserrat:wght@600&family=Roboto:wght@400;500&display=swap" rel="stylesheet">
<style>
  :root {
    --backdrop: #6a6666;
    --brand-plum: #885f70;
    --brand-plum-text: #8a5e6e;
    --card-white: #fbfbfb;
    --ink: #2b2b2b;
    --ink-soft: #555555;
    --rule: #7a8498;
  }
  * { margin: 0; padding: 0; box-sizing: border-box; }
  html, body {
    width: 1200px; height: 1200px; overflow: hidden;
    background: var(--backdrop);
  }
  .stage { position: relative; width: 1200px; height: 1200px; }

  .card {
    position: absolute;
    border-radius: 24px;
    overflow: hidden;
  }

  /* Front */
  .card-front {
    left: 238px; top: 118px; width: 712px; height: 420px;
    background: var(--brand-plum);
    display: flex; align-items: center; justify-content: center;
  }
  .front-wordmark {
    font-family: "Montserrat", sans-serif;
    font-weight: 600;
    font-size: 46px;
    letter-spacing: 1px;
    color: #ffffff;
    text-transform: uppercase;
    text-align: center;
    line-height: 1.1;
  }

  /* Back */
  .card-back {
    left: 231px; top: 645px; width: 711px; height: 415px;
    background: var(--card-white);
    font-family: "Roboto", sans-serif;
  }
  .back-wordmark {
    position: absolute; left: 40px; top: 118px;
    font-family: "Montserrat", sans-serif;
    font-weight: 600;
    font-size: 40px;
    line-height: 1.15;
    color: var(--brand-plum);
    text-transform: uppercase;
  }
  .person { position: absolute; left: 354px; top: 112px; }
  .person-name {
    font-family: "Montserrat", sans-serif;
    font-weight: 600; font-size: 24px;
    color: var(--brand-plum-text);
  }
  .person-role { font-size: 17px; color: var(--ink-soft); margin-top: 4px; }

  .contact-list {
    position: absolute; left: 354px; top: 190px;
    list-style: none;
  }
  .contact-list li {
    display: flex; align-items: center;
    font-size: 18px; color: var(--ink);
    height: 26px;
  }
  .contact-list svg { width: 16px; height: 16px; margin-right: 15px; fill: var(--brand-plum); }

  .social-row {
    position: absolute; left: 44px; right: 44px; top: 366px;
    display: flex; align-items: center; gap: 14px;
    font-size: 17px; color: var(--ink);
  }
  .social-row .rule { flex: 1; height: 1px; background: var(--rule); }
  .social-handle { display: flex; align-items: center; gap: 9px; }
  .social-dot { width: 15px; height: 15px; border-radius: 3px; background: var(--brand-plum); }
</style>
</head>
<body>
<main class="stage">
  <section class="card card-front" aria-label="Card front">
    <div class="front-wordmark">RW Office<br>Partners</div>
  </section>

  <section class="card card-back" aria-label="Card back">
    <div class="back-wordmark">RW Office<br>Partners</div>

    <div class="person">
      <div class="person-name">Marisol Wrenfield</div>
      <div class="person-role">Virtual Assistant</div>
    </div>

    <ul class="contact-list">
      <li>
        <svg viewBox="0 0 16 16" aria-hidden="true"><path d="M2 5c0-2 2-3 6-3s6 1 6 3v1h-3V5H5v1H2z"/><rect x="3" y="7" width="10" height="7" rx="1"/></svg>
        61 482 907 236
      </li>
      <li>
        <svg viewBox="0 0 16 16" aria-hidden="true"><path d="M1 3h14v10H1z M2 4l6 5 6-5" fill="none" stroke="#885f70" stroke-width="1.6"/></svg>
        marisol@rwofficepartners.com.au
      </li>
      <li>
        <svg viewBox="0 0 16 16" aria-hidden="true"><g fill="none" stroke="#885f70" stroke-width="1.3"><circle cx="8" cy="8" r="6.5"/><ellipse cx="8" cy="8" rx="2.8" ry="6.5"/><path d="M1.5 8h13"/></g></svg>
        www.rwofficepartners.com.au
      </li>
    </ul>

    <div class="social-row">
      <span class="rule"></span>
      <span class="social-handle"><span class="social-dot"></span>@rwofficepartners</span>
      <span class="social-handle"><span class="social-dot"></span>@rwofficepartners</span>
      <span class="rule"></span>
    </div>
  </section>
</main>
</body>
</html>
```